Anzeigengestaltung für Fliesenlegermeister
Zielgruppe
Ich bin ein Fliesenlegermeister und möchte mich selbstständig machen, ich saniere Bäder, Böden mit Fliesen, Fliesenspiegel und ich möchte eine Anzeige in den regionalen Zeitungen machen. Ich spreche alle Altersklassen mit Bädern für Sanierungen, Bodenfliesen und Neubauten an. Reparatur und Silikonarbeiten sowie Trockenbauarbeiten am eigenen Heim .
Aufgabenstellung
Ich möchte gern meine Kontaktdaten und die Farben vom Logo wieder finden,
als Beispiel habe ich meine aktuelle Visitenkarte beigefügt Dort finden sich die Kontaktdaten. Meine Arbeiten sind insbesondere :
Fliesenverlegung
Badsanierung
barrierefreie Bäder
Reparaturarbeiten
Silikonarbeiten
Trockenbau
Ob nun genau alle 6 Punkte in der Anzeige angezeigt werden soll bin ich mir nicht sicher oder ob nur 4 Beschreibungen reichen, damit es nicht zu viel wird.

```html
<!DOCTYPE html>
<html lang="de">
<head>
<meta charset="utf-8">
<title>Anzeigenvarianten Fliesenlegermeister</title>
<link href="https://fonts.googleapis.com/css2?family=Roboto:wght@400;500;700;900&display=swap" rel="stylesheet">
<style>
  :root{
    --blue:#0d4f9c;
    --grey:#4a4a4c;
    --text-grey:#4d4d4f;
    --white:#ffffff;
    --yellow:#ffe000;
    --tile-light:#d9b08c;
    --tile-dark:#8a6249;
  }
  *{box-sizing:border-box;margin:0;padding:0}
  html,body{width:1200px;height:1200px;overflow:hidden;background:var(--white);font-family:"Roboto",sans-serif}
  .canvas{position:relative;width:1200px;height:1200px}

  .size-label{position:absolute;top:367px;font-size:19px;font-weight:500;color:#222}
  .variant-letter{position:absolute;top:822px;font-size:50px;font-weight:900;color:#000;width:100px;text-align:center}

  .card{position:absolute;top:398px;height:406px;background:var(--grey)}
  .card__inner{position:absolute;left:5px;right:5px;top:5px;bottom:47px;background:var(--white);overflow:hidden}
  .card--a{left:71px;width:365px}
  .card--b{left:499px;width:284px}
  .card--c{left:848px;width:284px}

  .brand{position:absolute;display:flex;align-items:center}
  .brand__mark{background:var(--blue)}
  .brand__rule{width:2px;background:var(--grey)}
  .brand__name{font-weight:700;color:var(--blue);line-height:1;letter-spacing:0.5px}
  .brand__sub{font-weight:500;color:var(--text-grey);letter-spacing:1.6px;line-height:1;margin-top:4px}

  .photo{position:absolute;left:0;right:0;background:linear-gradient(160deg,#c9a184 0%,var(--tile-light) 45%,#b88866 75%,var(--tile-dark) 100%)}

  .sticker{position:absolute;border-radius:50%;background:var(--yellow);display:flex;align-items:center;justify-content:center;box-shadow:2px 3px 4px rgba(0,0,0,.25)}
  .sticker__text{transform:rotate(-20deg);color:var(--blue);font-weight:900;text-align:center;line-height:1}

  .services{position:absolute;list-style:none;font-weight:700}
  .services li{display:flex;align-items:center;white-space:nowrap}
  .services--blue{color:var(--blue)}
  .services--grey{color:var(--text-grey);text-align:right}
  .services--grey li{justify-content:flex-end}
  .diamond{display:inline-block;width:7px;height:7px;transform:rotate(45deg);flex:none}
  .services--blue .diamond{background:var(--blue);margin-right:7px}
  .services--grey .diamond{background:var(--text-grey);margin-left:7px}
  .services--stack{color:var(--text-grey)}
  .services--stack .diamond{background:var(--blue);margin-right:14px;width:8px;height:8px}

  .phone{position:absolute;display:flex;align-items:center;justify-content:center;color:var(--white);font-weight:700;gap:10px;border-radius:2px}
  .phone--land{background:var(--blue)}
  .phone--mobile{background:var(--grey)}
  .phone svg{flex:none}

  .contact{position:absolute;left:0;right:0;color:var(--text-grey);font-weight:500;text-align:center;line-height:1.25}
  .contact__line{display:flex;align-items:center;justify-content:center;gap:6px;white-space:nowrap}

  .footer{position:absolute;left:0;right:0;bottom:0;height:47px;color:var(--white);text-align:center}
  .footer__name{font-weight:700;font-size:20px;letter-spacing:1px;margin-top:3px}
  .footer__title{font-weight:400;letter-spacing:.5px}
</style>
</head>
<body>
<div class="canvas">

  <!-- Variant A -->
  <div class="size-label" style="left:71px">9x10cm</div>
  <div class="card card--a">
    <div class="card__inner">
      <div class="brand" style="left:12px;top:10px;height:55px">
        <div class="brand__mark" style="width:40px;height:40px;margin-right:34px"></div>
        <div class="brand__rule" style="height:50px;margin-right:10px"></div>
        <div>
          <div class="brand__name" style="font-size:27px">JONAS BREKEL</div>
          <div class="brand__sub" style="font-size:13px">FLIESENLEGERMEISTER</div>
        </div>
      </div>
      <div class="photo" role="img" aria-label="Foto: Hände markieren eine Fliese mit Bleistift und Winkel" style="top:68px;height:120px"></div>
      <div class="sticker" style="left:265px;top:79px;width:84px;height:84px">
        <div class="sticker__text" style="font-size:11px">KONTAKTIERE<br>UNS<br><span style="font-size:14px">JETZT!</span></div>
      </div>
      <ul class="services services--blue" style="left:10px;top:194px;font-size:17px;line-height:21px">
        <li><span class="diamond"></span>Badsanierung</li>
        <li><span class="diamond"></span>Fliesenverlegung</li>
        <li><span class="diamond"></span>barrierefreie Bäder</li>
      </ul>
      <ul class="services services--grey" style="right:10px;top:194px;font-size:17px;line-height:21px">
        <li>Trockenbau<span class="diamond"></span></li>
        <li>Silikonarbeiten<span class="diamond"></span></li>
        <li>Reparaturarbeiten<span class="diamond"></span></li>
      </ul>
      <div class="phone phone--land" style="left:0;top:263px;width:191px;height:35px;font-size:21px;gap:8px">
        <svg width="20" height="20" viewBox="0 0 24 24" fill="none" stroke="#fff" stroke-width="1.6"><path d="M5 3h4l2 5-2.5 1.5a11 11 0 0 0 6 6L16 13l5 2v4a2 2 0 0 1-2 2A16 16 0 0 1 3 5a2 2 0 0 1 2-2z"/></svg>
        05300/1234560
      </div>
      <div class="phone phone--mobile" style="left:194px;top:263px;width:161px;height:35px;font-size:21px;gap:6px">
        <svg width="13" height="20" viewBox="0 0 13 20" fill="none" stroke="#fff" stroke-width="1.4"><rect x="1" y="1" width="11" height="18" rx="2"/><line x1="5" y1="16" x2="8" y2="16"/></svg>
        01761234567
      </div>
      <div class="contact" style="top:305px;font-size:15px">
        <div class="contact__line">
          <svg width="12" height="17" viewBox="0 0 12 17" fill="none" stroke="#4d4d4f" stroke-width="1.3"><path d="M6 16C2 10 1 8 1 6a5 5 0 0 1 10 0c0 2-1 4-5 10z"/><circle cx="6" cy="6" r="2"/></svg>
          Lindenweg 7, 38100 Musterstadt
        </div>
        <div class="contact__line" style="margin-top:4px">
          <svg width="16" height="13" viewBox="0 0 16 13" fill="none" stroke="#4d4d4f" stroke-width="1.3"><rect x="1" y="1" width="14" height="11"/><path d="M1 1l7 6 7-6"/></svg>
          info@fliesenleger-brekel.de
        </div>
      </div>
    </div>
    <div class="footer">
      <div class="footer__name">Jonas Brekel</div>
      <div class="footer__title" style="font-size:14px">Bachelor Professional im Fliesenlegerhandwerk</div>
    </div>
  </div>
  <div class="variant-letter" style="left:203px">A</div>

  <!-- Variant B -->
  <div class="size-label" style="left:499px">7x10cm</div>
  <div class="card card--b">
    <div class="card__inner">
      <div class="brand" style="left:6px;top:6px;height:45px">
        <div class="brand__mark" style="width:34px;height:34px;margin-right:22px"></div>
        <div class="brand__rule" style="height:42px;margin-right:8px"></div>
        <div>
          <div class="brand__name" style="font-size:21px">JONAS BREKEL</div>
          <div class="brand__sub" style="font-size:10px;letter-spacing:1.3px">FLIESENLEGERMEISTER</div>
        </div>
      </div>
      <div class="photo" role="img" aria-label="Foto: Hände markieren eine Fliese mit Bleistift und Winkel" style="top:55px;height:91px"></div>
      <div class="sticker" style="left:191px;top:62px;width:74px;height:74px">
        <div class="sticker__text" style="font-size:10px">KONTAKTIERE<br>UNS<br><span style="font-size:12px">JETZT!</span></div>
      </div>
      <ul class="services services--blue" style="left:5px;top:150px;font-size:14px;line-height:17px">
        <li><span class="diamond" style="margin-right:4px"></span>Badsanierung</li>
        <li><span class="diamond" style="margin-right:4px"></span>Fliesenverlegung</li>
        <li><span class="diamond" style="margin-right:4px"></span>barrierefreie Bäder</li>
      </ul>
      <ul class="services services--grey" style="right:5px;top:150px;font-size:14px;line-height:17px">
        <li>Trockenbau<span class="diamond" style="margin-left:4px"></span></li>
        <li>Silikonarbeiten<span class="diamond" style="margin-left:4px"></span></li>
        <li>Reparaturarbeiten<span class="diamond" style="margin-left:4px"></span></li>
      </ul>
      <div class="phone phone--land" style="left:23px;top:205px;width:229px;height:42px;font-size:25px">
        <svg width="24" height="24" viewBox="0 0 24 24" fill="none" stroke="#fff" stroke-width="1.6"><path d="M5 3h4l2 5-2.5 1.5a11 11 0 0 0 6 6L16 13l5 2v4a2 2 0 0 1-2 2A16 16 0 0 1 3 5a2 2 0 0 1 2-2z"/></svg>
        05300/1234560
      </div>
      <div class="phone phone--mobile" style="left:23px;top:252px;width:229px;height:42px;font-size:25px;gap:14px">
        <svg width="16" height="26" viewBox="0 0 13 20" fill="none" stroke="#fff" stroke-width="1.2"><rect x="1" y="1" width="11" height="18" rx="2"/><line x1="5" y1="16" x2="8" y2="16"/></svg>
        01761234567
      </div>
      <div class="contact" style="top:297px;font-size:15px;line-height:19px">
        <div class="contact__line">
          <svg width="12" height="16" viewBox="0 0 12 17" fill="none" stroke="#4d4d4f" stroke-width="1.3"><path d="M6 16C2 10 1 8 1 6a5 5 0 0 1 10 0c0 2-1 4-5 10z"/><circle cx="6" cy="6" r="2"/></svg>
          Lindenweg 7,
        </div>
        <div class="contact__line">38100 Musterstadt</div>
        <div class="contact__line">
          <svg width="14" height="12" viewBox="0 0 16 13" fill="none" stroke="#4d4d4f" stroke-width="1.3"><rect x="1" y="1" width="14" height="11"/><path d="M1 1l7 6 7-6"/></svg>
          info@fliesenleger-brekel.de
        </div>
      </div>
    </div>
    <div class="footer">
      <div class="footer__name">Jonas Brekel</div>
      <div class="footer__title" style="font-size:11px">Bachelor Professional im Fliesenlegerhandwerk</div>
    </div>
  </div>
  <div class="variant-letter" style="left:591px">B</div>

  <!-- Variant C -->
  <div class="size-label" style="left:848px">7x10cm</div>
  <div class="card card--c">
    <div class="card__inner">
      <div class="brand" style="left:6px;top:6px;height:45px">
        <div class="brand__mark" style="width:34px;height:34px;margin-right:22px"></div>
        <div class="brand__rule" style="height:42px;margin-right:8px"></div>
        <div>
          <div class="brand__name" style="font-size:21px">JONAS BREKEL</div>
          <div class="brand__sub" style="font-size:10px;letter-spacing:1.3px">FLIESENLEGERMEISTER</div>
        </div>
      </div>
      <ul class="services services--stack" style="left:20px;top:68px;font-size:17px;line-height:20.6px">
        <li><span class="diamond"></span>barrierefreie Bäder</li>
        <li><span class="diamond"></span>Fliesenverlegung</li>
        <li><span class="diamond"></span>Badsanierung</li>
        <li><span class="diamond"></span>Trockenbau</li>
        <li><span class="diamond"></span>Silikonarbeiten</li>
        <li><span class="diamond"></span>Reparaturarbeiten</li>
      </ul>
      <div class="sticker" style="left:174px;top:88px;width:88px;height:88px">
        <div class="sticker__text" style="font-size:11px">KONTAKTIERE<br>UNS<br><span style="font-size:14px">JETZT!</span></div>
      </div>
      <div class="phone phone--land" style="left:20px;top:198px;width:239px;height:44px;font-size:26px">
        <svg width="24" height="24" viewBox="0 0 24 24" fill="none" stroke="#fff" stroke-width="1.6"><path d="M5 3h4l2 5-2.5 1.5a11 11 0 0 0 6 6L16 13l5 2v4a2 2 0 0 1-2 2A16 16 0 0 1 3 5a2 2 0 0 1 2-2z"/></svg>
        05300/1234560
      </div>
      <div class="phone phone--mobile" style="left:20px;top:247px;width:239px;height:44px;font-size:26px;gap:16px">
        <svg width="16" height="26" viewBox="0 0 13 20" fill="none" stroke="#fff" stroke-width="1.2"><rect x="1" y="1" width="11" height="18" rx="2"/><line x1="5" y1="16" x2="8" y2="16"/></svg>
        01761234567
      </div>
      <div class="contact" style="top:297px;font-size:15px;line-height:19px">
        <div class="contact__line">
          <svg width="12" height="16" viewBox="0 0 12 17" fill="none" stroke="#4d4d4f" stroke-width="1.3"><path d="M6 16C2 10 1 8 1 6a5 5 0 0 1 10 0c0 2-1 4-5 10z"/><circle cx="6" cy="6" r="2"/></svg>
          Lindenweg 7,
        </div>
        <div class="contact__line">38100 Musterstadt</div>
        <div class="contact__line">
          <svg width="14" height="12" viewBox="0 0 16 13" fill="none" stroke="#4d4d4f" stroke-width="1.3"><rect x="1" y="1" width="14" height="11"/><path d="M1 1l7 6 7-6"/></svg>
          info@fliesenleger-brekel.de
        </div>
      </div>
    </div>
    <div class="footer">
      <div class="footer__name">Jonas Brekel</div>
      <div class="footer__title" style="font-size:11px">Bachelor Professional im Fliesenlegerhandwerk</div>
    </div>
  </div>
  <div class="variant-letter" style="left:940px">C</div>

</div>
</body>
</html>
```